NimbaVault Website Homepage Design

Please provide your idea of homepage for a hosting company. This project is for DESIGN only, no coding.

It must use/combine colors used in logo, clean, modern look.

Homepage must consist of at least 4 sections (example: testimonials, services, and so on. not necesarily all of them). We would like the navigation to be horizontal, but not mandatory.

You can include a preview of services page (optional, not a must).

Number of Pages Required

1 page

Font styles to use
Sans Serif

```html
<!DOCTYPE html>
<html lang="en">
<head>
<meta charset="utf-8">
<title>NimbaVault – Hosting</title>
<link href="https://fonts.googleapis.com/css2?family=Questrial&family=Hind:wght@400;500;600&display=swap" rel="stylesheet">
<style>
:root{
  --navy:#0a1566;
  --navy-deep:#070f4d;
  --blue:#0a7be0;
  --blue-bright:#1188f0;
  --lavender:#dde2fb;
  --white:#ffffff;
  --ink:#1c1c2a;
  --muted:#3b3b4d;
}
*{margin:0;padding:0;box-sizing:border-box}
html,body{width:1200px;height:4175px;overflow:hidden}
body{position:relative;background:var(--white);font-family:"Hind",sans-serif;color:var(--ink)}
.abs{position:absolute}
.heading{font-family:"Questrial",sans-serif;font-weight:400}
.btn{position:absolute;display:flex;align-items:center;justify-content:center;border-radius:30px;background:var(--blue);color:var(--white);font-family:"Questrial",sans-serif;font-size:17px}

/* hero */
.hero{left:0;top:0;width:1200px;height:960px;background:radial-gradient(ellipse at 70% 35%,#1a2a9a 0%,var(--navy) 55%,var(--navy-deep) 100%)}
.brand{font-family:"Questrial",sans-serif;color:var(--white);letter-spacing:3px;display:flex;align-items:center;gap:10px}
.brand-dot{width:14px;height:14px;border-radius:50%;background:var(--white)}
.nav{top:46px;left:538px;display:flex;gap:22px;font-family:"Hind",sans-serif;font-weight:600;font-size:15px;color:var(--white)}
.hero-title{left:172px;top:196px;font-size:50px;color:var(--white);font-weight:600;font-family:"Hind",sans-serif}
.hero-sub{left:172px;top:278px;width:360px;font-size:19px;line-height:31px;color:var(--white);font-weight:500}
.hero-art{left:592px;top:105px;width:527px;height:665px;border-radius:40px;background:radial-gradient(circle at 55% 45%,#c9d6f7 0%,#5a7fe0 45%,rgba(20,40,150,0) 75%)}

/* about */
.about{left:0;top:960px;width:1200px;height:586px;background:var(--lavender)}
.about-art{left:78px;top:990px;width:457px;height:454px;border-radius:30px;background:radial-gradient(circle at 45% 50%,#7fa1ef 0%,#a9bcf4 45%,rgba(221,226,251,0) 75%)}
.section-title{font-size:33px;color:var(--ink)}
.para{font-size:12.5px;line-height:24px;color:var(--muted)}

/* services */
.card{position:absolute;width:263px;height:412px;border-radius:132px;background:var(--white);box-shadow:0 10px 28px rgba(20,30,90,.14);border-top:6px solid var(--blue);text-align:center;padding:0 16px}
.card-name{font-family:"Questrial",sans-serif;font-size:21px;margin-top:10px}
.card-text{font-size:13px;line-height:23px;margin-top:12px;color:var(--muted)}
.card .btn{position:relative;margin:24px auto 0;width:108px;height:46px;font-family:"Hind",sans-serif;font-weight:600;font-size:13px}
.card-icon{margin-top:64px}
.card.featured{background:linear-gradient(180deg,#0b7fe3 0%,#0a3fa8 55%,var(--navy) 100%);border-top:none;border-bottom:12px solid #2a8de0;color:var(--white)}
.card.featured .card-text{color:#e8efff}
.card.featured .btn{background:var(--white);color:var(--navy)}

/* features */
.features{left:0;top:2279px;width:1200px;height:529px;background:linear-gradient(90deg,#050b3a 0%,#0a1a6a 55%,#0c2a8a 100%)}
.features-art{left:650px;top:2279px;width:550px;height:529px;background:radial-gradient(circle at 50% 55%,#3aa8ff 0%,#1560d8 35%,rgba(12,42,138,0) 75%)}

/* testimonials */
.quote-card{position:absolute;top:2997px;width:407px;height:211px;border-radius:12px;background:var(--white);box-shadow:0 8px 30px rgba(20,30,90,.14);padding:30px 18px 0 120px}
.quote-card.dark{background:linear-gradient(180deg,#0a6fd6 0%,var(--navy) 100%);color:var(--white)}
.avatar{position:absolute;left:14px;top:26px;width:82px;height:82px;border-radius:50%;background:radial-gradient(circle at 50% 40%,#c9a58a,#6b4a3a)}
.mark{position:absolute;left:28px;top:118px;font-family:"Questrial",sans-serif;font-size:90px;line-height:1;color:var(--blue);font-style:italic}
.quote-card.dark .mark{color:var(--white)}
.q-name{font-size:15px;font-weight:500}
.q-text{font-size:12px;line-height:23.5px;margin-top:8px;color:var(--muted)}
.quote-card.dark .q-text{color:#e1e9ff}
.tail{position:absolute;bottom:-38px;left:44px;width:0;height:0;border-right:60px solid transparent;border-top:40px solid var(--white)}
.quote-card.dark .tail{border-top-color:var(--navy)}

/* footer */
.footer{left:0;top:3598px;width:1200px;height:577px;background:var(--navy)}
.social{position:absolute;top:3645px;width:42px;height:42px;border-radius:50%;background:var(--white)}
.f-head{font-family:"Questrial",sans-serif;font-size:22px;color:var(--white)}
.f-links{list-style:none;font-size:14px;line-height:28.5px;color:var(--white)}
.email{left:795px;top:3890px;width:232px;height:47px;border-radius:24px;background:var(--white);font-size:13px;padding-left:16px;display:flex;align-items:center;color:var(--ink)}
</style>
</head>
<body>

<!-- Hero -->
<div class="abs hero"></div>
<div class="abs brand" style="left:172px;top:34px;font-size:40px"><span class="brand-dot"></span>NIMBAVAULT</div>
<nav class="abs nav"><span>HOME</span><span>ABOUT US</span><span>SERVICES</span><span>BLOG</span><span>FEATURES</span><span>CONTACT US</span></nav>
<h1 class="abs hero-title">NimbaVault</h1>
<p class="abs hero-sub">Nemo enim ipsam voluptatem quia voluptas sit...</p>
<div class="btn" style="left:172px;top:370px;width:141px;height:63px;font-size:19px">Sign up Here</div>
<div class="abs hero-art" role="img" aria-label="Isometric illustration of servers, cloud storage and people working"></div>

<svg class="abs" style="left:0;top:690px" width="1200" height="300" viewBox="0 0 1200 300" aria-hidden="true">
  <path d="M0 120 C180 20 320 60 470 150 C650 260 850 280 1010 200 C1120 145 1170 95 1200 70 L1200 300 L0 300Z" fill="var(--blue)"/>
  <path d="M0 140 C180 50 320 90 470 170 C650 255 850 265 1010 195 C1120 145 1170 110 1200 95 L1200 300 L0 300Z" fill="var(--lavender)"/>
</svg>

<!-- About -->
<div class="abs about"></div>
<div class="abs about-art" role="img" aria-label="Isometric illustration of a laptop, server stack and team members"></div>
<h2 class="abs heading section-title" style="left:585px;top:1058px">About NimbaVault</h2>
<p class="abs para" style="left:585px;top:1124px;width:444px">Nam libero tempore, cum soluta nobis est eligendi optio cumque nihil impedit quo minus id quod maxime placeat facere possimus, omnis voluptas assumenda est, omnis dolor re pellendus. Temporibus autem quibusdam et aut officiis debitis aut rerum necessitatibus saepe eveniet ut et voluptates repudiandae sint et molestiae non recusandae. Itaque earum rerum hic tenetur.</p>
<div class="btn" style="left:585px;top:1278px;width:122px;height:50px">Read More</div>

<!-- Services -->
<h2 class="abs heading section-title" style="left:0;width:1200px;text-align:center;top:1626px">Our Services</h2>

<div class="card" style="left:172px;top:1700px">
  <svg class="card-icon" width="70" height="76" viewBox="0 0 70 76" fill="none" stroke="var(--ink)" stroke-width="2.5" aria-hidden="true">
    <rect x="18" y="4" width="34" height="10" rx="2"/><rect x="18" y="17" width="34" height="10" rx="2"/><rect x="18" y="30" width="34" height="10" rx="2"/>
    <path d="M3 52h14v20H3z M17 56c10-4 20-2 28 2l20-6c2 2 1 5-2 6L40 70H17"/>
  </svg>
  <div class="card-name">Web Hosting</div>
  <p class="card-text">Nam libero tempore, cum soluta nobis est eligendi optio cumque nihil impedit quo minus id quod.</p>
  <div class="btn">READ MORE</div>
</div>

<div class="card featured" style="left:469px;top:1760px">
  <svg class="card-icon" style="margin-top:50px" width="70" height="80" viewBox="0 0 70 80" fill="none" stroke="var(--white)" stroke-width="2.5" aria-hidden="true">
    <rect x="12" y="4" width="46" height="14" rx="3"/><rect x="12" y="22" width="46" height="14" rx="3"/><rect x="12" y="40" width="46" height="14" rx="3"/>
    <path d="M35 54v14 M4 74h62"/><circle cx="35" cy="72" r="3"/>
  </svg>
  <div class="card-name">SiteCraft Hosting</div>
  <p class="card-text">Nam libero tempore, cum soluta nobis est eligendi optio cumque nihil impedit quo minus id quod.</p>
  <div class="btn">READ MORE</div>
</div>

<div class="card" style="left:764px;top:1700px">
  <svg class="card-icon" width="86" height="76" viewBox="0 0 86 76" fill="none" stroke="var(--ink)" stroke-width="2.5" aria-hidden="true">
    <path d="M20 62C8 62 4 52 8 45c3-5 8-6 12-5 0-14 12-24 25-20 7 2 11 7 12 12 10-2 20 5 20 16 0 8-6 14-14 14z"/>
    <circle cx="43" cy="42" r="5"/><circle cx="30" cy="46" r="4"/><circle cx="56" cy="46" r="4"/>
    <path d="M33 60c0-8 20-8 20 0 M22 58c0-6 12-6 12-2 M52 56c0-4 12-4 12 2"/>
  </svg>
  <div class="card-name">Cloud Hosting</div>
  <p class="card-text">Nam libero tempore, cum soluta nobis est eligendi optio cumque nihil impedit quo minus id quod.</p>
  <div class="btn">READ MORE</div>
</div>

<!-- Features -->
<div class="abs features"></div>
<div class="abs features-art" role="img" aria-label="Glowing cloud and server rack over a data centre background"></div>
<h2 class="abs heading" style="left:172px;top:2400px;font-size:33px;color:var(--white)">NimbaVault Features</h2>
<p class="abs para" style="left:172px;top:2466px;width:448px;color:#e6ebff">Nam libero tempore, cum soluta nobis est eligendi optio cumque nihil impedit quo minus id quod maxime placeat facere possimus, omnis voluptas assumenda est, omnis dolor re pellendus. Temporibus autem quibusdam et aut officiis debitis aut rerum necessitatibus saepe eveniet ut et voluptates repudiandae sint et molestiae non recusandae. Itaque earum rerum hic tenetur.</p>
<div class="btn" style="left:173px;top:2619px;width:122px;height:50px">Read More</div>

<!-- Testimonials -->
<h2 class="abs heading section-title" style="left:0;width:1200px;text-align:center;top:2886px">Our Testimonials</h2>

<div class="quote-card" style="left:172px">
  <div class="avatar" role="img" aria-label="Portrait photo of the reviewer"></div>
  <div class="mark">“</div>
  <div class="q-name">Marla Jennings</div>
  <p class="q-text">Nam libero tempore, cum soluta nobis est eligendi optio cumque nihil im pedit quo minus id quod maxime placeat facere possimus, omnis volup tas assumenda...</p>
  <span class="tail"></span>
</div>

<div class="quote-card dark" style="left:620px">
  <div class="avatar" role="img" aria-label="Portrait photo of the reviewer"></div>
  <div class="mark">“</div>
  <div class="q-name">Desmond</div>
  <p class="q-text">Nam libero tempore, cum soluta nobis est eligendi optio cumque nihil im pedit quo minus id quod maxime placeat facere possimus, omnis volup tas assumenda...</p>
  <span class="tail"></span>
</div>

<!-- Footer -->
<div class="abs footer"></div>
<svg class="abs" style="left:0;top:3300px" width="1200" height="300" viewBox="0 0 1200 300" aria-hidden="true">
  <path d="M0 200 C150 80 300 30 420 40 C600 60 760 230 900 250 C1030 265 1130 200 1200 160 L1200 300 L0 300Z" fill="var(--blue)"/>
  <path d="M0 225 C150 110 300 60 420 68 C600 85 760 245 900 262 C1030 275 1130 220 1200 185 L1200 300 L0 300Z" fill="var(--navy)"/>
</svg>
<svg class="abs" style="left:880px;top:3415px" width="82" height="82" viewBox="0 0 82 82" aria-label="Back to top" role="img">
  <circle cx="41" cy="41" r="41" fill="var(--blue-bright)"/>
  <path d="M41 60V22 M27 36l14-14 14 14" stroke="var(--white)" stroke-width="5" fill="none" stroke-linecap="round" stroke-linejoin="round"/>
</svg>

<div class="abs brand" style="left:172px;top:3640px;font-size:52px"><span class="brand-dot" style="width:18px;height:18px"></span>NIMBAVAULT</div>
<span class="social" style="left:711px" aria-label="Social link"></span>
<span class="social" style="left:780px" aria-label="Social link"></span>
<span class="social" style="left:848px" aria-label="Social link"></span>
<span class="social" style="left:917px" aria-label="Social link"></span>
<span class="social" style="left:985px" aria-label="Social link"></span>

<h3 class="abs f-head" style="left:172px;top:3782px">Quick Links</h3>
<ul class="abs f-links" style="left:172px;top:3830px"><li>Home</li><li>About Us</li><li>Services</li><li>blog</li><li>Features</li><li>Contact</li></ul>
<ul class="abs f-links" style="left:307px;top:3830px"><li>Web Hosting</li><li>Kernix VPS Hosting</li><li>NVMe Hosting</li><li>Custom SSD VPS</li><li>Cloud Dedicated Servers</li><li>Hosting Solutions</li></ul>
<h3 class="abs f-head" style="left:562px;top:3782px">Top Links</h3>
<ul class="abs f-links" style="left:562px;top:3830px"><li>Privacy Policy</li><li>Terms &amp; Conditions</li><li>Customer Reviews</li><li>Awards &amp; Recognition</li><li>Our Policies</li></ul>
<h3 class="abs f-head" style="left:795px;top:3782px">Newsletter Signup</h3>
<p class="abs" style="left:795px;top:3830px;width:240px;font-size:14px;line-height:22px;color:var(--white)">Nam libero tempore, cum soluta nobis eligendis</p>
<div class="abs email">Email Address</div>
<div class="btn" style="left:795px;top:3951px;width:110px;height:47px;font-family:'Hind',sans-serif;font-size:14px">Subscribe</div>

<div class="abs" style="left:172px;top:4076px;width:855px;height:1px;background:rgba(255,255,255,.55)"></div>
<p class="abs" style="left:0;width:1200px;top:4114px;text-align:center;font-size:15px;color:var(--white)">Copyrights @ 2021 NimbaVault. All Rights Reserved.</p>

</body>
</html>
```